Modern design company business card design

We are a design oriented construction firm. The owner is an architect and licensed General Contractor and accomplished furniture designer. We do new home construction and large scale remodeling and office design. We would like a design for our new business cards that is clean and modern, but relatable. We like the bright green color of our logo mixed with different shades of grey. We're also open to reinterpreting the logo.

Target Market(s)

Potential design clients,
Construction clients

Industry/Entity Type

Architecture

Contact Information for Business Card

Tall Maple Design | Build Inc. (optional with logo, Inc. optional)Jeffrey MorganOwner (optional)317.555.0148 cell317.431.8056 officejmorgan@greensquareinc.comwww.greensquareinc.com

Font styles to use
Sans Serif
Other font styles liked:
• Avenir

Requirements
Nice to have
• I like designs that have some continuity between the front and back, i.e. similar layouts or graphic elements that wrap around the card. I tend to prefer horizontal over vertical, but that's not a have to. I also tend to prefer white or recycled paper.

```html
<!DOCTYPE html>
<html lang="en">
<head>
<meta charset="utf-8">
<title>Tall Maple Design | Build – Business Card</title>
<link href="https://fonts.googleapis.com/css2?family=Nunito+Sans:wght@400;700&display=swap" rel="stylesheet">
<style>
  :root {
    --page-bg: #e9e9e7;
    --card-white: #ffffff;
    --green-light: #c4dd68;
    --green-deep: #6bbf4a;
    --brand-green: #8fcc55;
    --grey-text: #7e7e7e;
    --white-text: #ffffff;
  }
  * { box-sizing: border-box; margin: 0; padding: 0; }
  html, body {
    width: 1200px; height: 900px; overflow: hidden;
    background: var(--page-bg);
    font-family: "Nunito Sans", "Avenir", sans-serif;
  }
  .canvas { position: relative; width: 1200px; height: 900px; }

  .card {
    position: absolute;
    background: var(--card-white);
    border-radius: 16px;
    overflow: hidden;
    box-shadow: 0 6px 22px rgba(0,0,0,0.12);
  }

  /* Front */
  .card--front { left: 78px; top: 35px; width: 588px; height: 362px; }
  .front__block {
    position: absolute;
    background: linear-gradient(180deg, var(--green-light) 0%, var(--green-light) 30%, var(--green-deep) 100%);
  }
  .front__block--corner { left: 0; top: 0; width: 272px; height: 238px; }
  .front__block--contact { left: 294px; top: 128px; width: 294px; height: 234px; }

  .contact {
    position: absolute; right: 36px; top: 166px;
    text-align: right; color: var(--white-text);
  }
  .contact__name { font-weight: 700; font-size: 19px; line-height: 24px; }
  .contact__role { font-size: 15px; line-height: 18px; margin-bottom: 25px; }
  .contact__list { list-style: none; }
  .contact__item {
    display: flex; justify-content: flex-end; align-items: center; gap: 7px;
    font-size: 15px; line-height: 24.5px; white-space: nowrap;
  }
  .contact__icon { width: 12px; height: 12px; fill: var(--white-text); flex: none; }

  /* Back */
  .card--back { left: 389px; top: 506px; width: 565px; height: 350px; }
  .back__name {
    position: absolute; left: 0; right: 0; top: 0; bottom: 0;
    display: flex; align-items: center; justify-content: center; gap: 14px;
    color: var(--grey-text); font-weight: 400; font-size: 24px; white-space: nowrap;
  }
  .back__dot {
    width: 22px; height: 22px; border-radius: 50%;
    background: var(--brand-green); flex: none;
  }
</style>
</head>
<body>
<main class="canvas">

  <section class="card card--front" aria-label="Card front">
    <div class="front__block front__block--corner"></div>
    <div class="front__block front__block--contact"></div>
    <div class="contact">
      <p class="contact__name">Dennis Holloway</p>
      <p class="contact__role">Owner</p>
      <ul class="contact__list">
        <li class="contact__item">317.555.0172
          <svg class="contact__icon" viewBox="0 0 24 24" aria-hidden="true"><path d="M6.6 10.8a15.1 15.1 0 0 0 6.6 6.6l2.2-2.2a1 1 0 0 1 1-.25 11.4 11.4 0 0 0 3.6.57 1 1 0 0 1 1 1V20a1 1 0 0 1-1 1A17 17 0 0 1 3 4a1 1 0 0 1 1-1h3.5a1 1 0 0 1 1 1c0 1.25.2 2.45.57 3.57a1 1 0 0 1-.25 1z"/></svg>
        </li>
        <li class="contact__item">317.555.0148
          <svg class="contact__icon" viewBox="0 0 24 24" aria-hidden="true"><path d="M7 1h10a2 2 0 0 1 2 2v18a2 2 0 0 1-2 2H7a2 2 0 0 1-2-2V3a2 2 0 0 1 2-2zm0 3v14h10V4zm5 15.5a1 1 0 1 0 0 2 1 1 0 0 0 0-2z"/></svg>
        </li>
        <li class="contact__item">dholloway@tallmapleinc.example
          <svg class="contact__icon" viewBox="0 0 24 24" aria-hidden="true"><path d="M2 5h20v14H2zm2 2v.5l8 5 8-5V7l-8 5z"/></svg>
        </li>
        <li class="contact__item">www.tallmapleinc.example
          <svg class="contact__icon" viewBox="0 0 24 24" aria-hidden="true"><path d="M10.6 13.4a1 1 0 0 1 0-1.4l3.5-3.5a1 1 0 1 1 1.4 1.4L12 13.4a1 1 0 0 1-1.4 0zM8 21a5 5 0 0 1-3.5-8.5l2.1-2.1 1.4 1.4-2.1 2.1a3 3 0 0 0 4.2 4.2l2.1-2.1 1.4 1.4-2.1 2.1A5 5 0 0 1 8 21zm9.4-7.6-1.4-1.4 2.1-2.1a3 3 0 0 0-4.2-4.2l-2.1 2.1-1.4-1.4 2.1-2.1a5 5 0 0 1 7 7z"/></svg>
        </li>
      </ul>
    </div>
  </section>

  <section class="card card--back" aria-label="Card back">
    <div class="back__name">
      <span class="back__dot" aria-hidden="true"></span>
      <span>Tall Maple Design | Build</span>
    </div>
  </section>

</main>
</body>
</html>
```